Pinecrest Capital Group - Company Envelopes

I am looking for a graphic designer to create a bespoke envelope for my company use, which I can then have printed at scale. The envelope should be of standard size and shape, but Matt black in colour, with semi-thick vertical gloss (shiny) lines going from left to right, but must stop to the right of the envelope, leaving a Matt black line with enough space for a stamp in the top right corner. The back of the envelope should be full Matt black.

Requirements
Must have
• Must be as described in brief
Should not have
• No other colours - Just Matt and Gloss Black

```html
<!DOCTYPE html>
<html lang="en">
<head>
<meta charset="utf-8">
<title>Pinecrest Capital Group – Company Envelopes</title>
<link rel="stylesheet" href="https://fonts.googleapis.com/css2?family=Libre+Baskerville:wght@700&display=swap">
<style>
  :root {
    --backdrop: #5e5e5e;
    --matt-black: #060606;
    --stamp-area: #1b1b1b;
    --flap-edge: #bdbdbd;
    --name-white: #ffffff;
    --gloss-1: #2f2f2f;
    --gloss-2: #3a3a3a;
    --gloss-3: #343434;
    --gloss-4: #3e3e3e;
    --gloss-5: #7c7c7c;
    --gloss-6: #898989;
    --gloss-7: #959595;
    --gloss-8: #a0a0a0;
    --gloss-9: #a8a8a8;
    --gloss-10: #aeaeae;
    --gloss-11: #b6b6b6;
  }
  * { margin: 0; padding: 0; box-sizing: border-box; }
  html, body {
    width: 1200px; height: 895px; overflow: hidden;
    background: var(--backdrop);
  }
  .canvas { position: relative; width: 1200px; height: 895px; }

  .envelope {
    position: absolute; left: 364px; width: 472px; height: 333px;
    background: var(--matt-black);
    overflow: hidden;
  }
  .envelope--back { top: 92px; }
  .envelope--front { top: 469px; }

  .flap { position: absolute; left: 0; top: 0; width: 472px; height: 80px; }

  .brand-name {
    position: absolute; left: 0; right: 0;
    font-family: "Libre Baskerville", "Times New Roman", serif;
    font-weight: 700; color: var(--name-white);
    text-align: center;
  }
  .brand-name--back { top: 170px; }
  .brand-name__main { display: block; font-size: 36px; line-height: 1; letter-spacing: 1px; }
  .brand-name__sub { display: block; font-size: 12px; letter-spacing: 5px; margin-top: 6px; }

  .stamp-area {
    position: absolute; left: 318px; top: 33px; width: 126px; height: 126px;
    background: var(--stamp-area);
  }

  .gloss-stripe {
    position: absolute; top: 160px; width: 32px; height: 173px;
    background-image: linear-gradient(180deg, rgba(255,255,255,0.06), rgba(0,0,0,0.08));
  }
  .gloss-stripe--short { height: 111px; }

  .brand-name--front {
    left: 15px; right: auto; top: 278px; width: 150px; text-align: left;
  }
  .brand-name--front .brand-name__main { font-size: 17px; letter-spacing: 0.3px; }
  .brand-name--front .brand-name__sub { font-size: 6px; letter-spacing: 2.4px; margin-top: 3px; }
</style>
</head>
<body>
<div class="canvas">

  <section class="envelope envelope--back" aria-label="Envelope back">
    <svg class="flap" viewBox="0 0 472 80" aria-hidden="true">
      <path d="M0,0 L17,58 Q23,75 40,75 L432,75 Q449,75 455,58 L472,0"
            fill="none" stroke="var(--flap-edge)" stroke-width="0.8"/>
    </svg>
    <div class="brand-name brand-name--back">
      <span class="brand-name__main">PINECREST</span>
      <span class="brand-name__sub">CAPITAL GROUP</span>
    </div>
  </section>

  <section class="envelope envelope--front" aria-label="Envelope front">
    <div class="stamp-area"></div>

    <div class="gloss-stripe gloss-stripe--short" style="left:0;background-color:var(--gloss-1)"></div>
    <div class="gloss-stripe gloss-stripe--short" style="left:44px;background-color:var(--gloss-2)"></div>
    <div class="gloss-stripe gloss-stripe--short" style="left:88px;background-color:var(--gloss-3)"></div>
    <div class="gloss-stripe gloss-stripe--short" style="left:132px;background-color:var(--gloss-4)"></div>
    <div class="gloss-stripe" style="left:176px;background-color:var(--gloss-5)"></div>
    <div class="gloss-stripe" style="left:220px;background-color:var(--gloss-6)"></div>
    <div class="gloss-stripe" style="left:264px;background-color:var(--gloss-7)"></div>
    <div class="gloss-stripe" style="left:308px;background-color:var(--gloss-8)"></div>
    <div class="gloss-stripe" style="left:352px;background-color:var(--gloss-9)"></div>
    <div class="gloss-stripe" style="left:396px;background-color:var(--gloss-10)"></div>
    <div class="gloss-stripe" style="left:440px;background-color:var(--gloss-11)"></div>

    <div class="brand-name brand-name--front">
      <span class="brand-name__main">PINECREST</span>
      <span class="brand-name__sub">CAPITAL GROUP</span>
    </div>
  </section>

</div>
</body>
</html>
```